Corvane Capital Business Cards

These are professional business cards that are for my family office.
Put fake emails and phone numbers as of now until I finalize those components. This family office controls my families investments, assets, and future. The cards should be professional.
..
.
.
.
I just uploaded another variation of a logo I would like to see as a business card to I am inbeteen which logo to use

Target Market(s)

business

Industry/Entity Type

business

Contact Information for Business Card

Professional, wealth related, finance related.

Requirements
Must have
• Logo

```html
<!DOCTYPE html>
<html lang="en">
<head>
<meta charset="utf-8">
<title>Corvane Capital Business Cards</title>
<link href="https://fonts.googleapis.com/css2?family=Tinos:wght@400;700&display=swap" rel="stylesheet">
<style>
  :root {
    --backdrop: #3a3a3c;
    --navy: #22252f;
    --navy-band: #2d3039;
    --navy-deep: #1c1f29;
    --paper: #ffffff;
    --ink: #1f222c;
    --rule: #6b6d74;
    --dot-grey: #a9a9ad;
    --light: #f2f2f4;
  }
  * { box-sizing: border-box; margin: 0; padding: 0; }
  html, body { width: 1200px; height: 694px; overflow: hidden; }
  body {
    background: var(--backdrop);
    font-family: "Tinos", "Times New Roman", serif;
    position: relative;
  }
  .card {
    position: absolute;
    top: 192px;
    width: 540px;
    height: 310px;
    border-radius: 22px;
    overflow: hidden;
    box-shadow: 0 12px 30px rgba(0,0,0,.35);
  }
  /* Back side */
  .card-back { left: 40px; background: var(--navy); }
  .monogram-pattern {
    position: absolute; inset: 0;
    background: radial-gradient(circle at 50% 45%, #2a2e3b 0%, var(--navy) 55%, var(--navy-deep) 100%);
  }
  .back-mark {
    position: absolute; left: 50%; top: 50%;
    transform: translate(-50%, -50%);
    display: flex; align-items: center; gap: 10px;
    color: var(--light);
  }
  .back-mark .mark-circle {
    width: 26px; height: 26px; border-radius: 50%;
    border: 2px solid var(--light);
  }
  .back-mark .mark-name { font-size: 17px; letter-spacing: 3px; text-transform: uppercase; }

  /* Front side */
  .card-front { left: 620px; background: var(--paper); }
  .front-band {
    position: absolute; left: 0; right: 0; bottom: 0; height: 78px;
    background: var(--navy-band);
  }
  .brand-block {
    position: absolute; left: 28px; top: 70px; width: 220px;
    display: flex; flex-direction: column; align-items: center; gap: 14px;
    color: var(--ink);
  }
  .brand-circle {
    width: 96px; height: 96px; border-radius: 50%;
    border: 3px solid var(--ink);
  }
  .brand-name { font-size: 21px; letter-spacing: 2.5px; text-transform: uppercase; }
  .divider {
    position: absolute; left: 262px; top: 28px; width: 1px; height: 184px;
    background: var(--rule);
  }
  .contact-block {
    position: absolute; left: 284px; top: 26px; color: var(--ink);
  }
  .person-name { font-size: 22px; font-weight: 700; }
  .person-role { font-size: 13px; margin-bottom: 12px; }
  .address { font-size: 13.5px; line-height: 1.3; margin-bottom: 14px; }
  .contact-list { list-style: none; font-size: 13.5px; line-height: 1.45; }
  .contact-list li { display: flex; align-items: center; gap: 8px; }
  .contact-list svg { width: 13px; height: 13px; fill: var(--ink); flex: none; }
  .band-mark {
    position: absolute; right: 42px; bottom: 18px;
    display: flex; align-items: center; gap: 10px; color: var(--light);
  }
  .band-mark .mark-circle {
    width: 40px; height: 40px; border-radius: 50%; border: 2px solid var(--light);
  }
  .band-mark .mark-name { font-size: 14px; letter-spacing: 2px; text-transform: uppercase; }
</style>
</head>
<body>
  <section class="card card-back">
    <div class="monogram-pattern" role="img" aria-label="Embossed repeating monogram pattern in dark navy"></div>
    <div class="back-mark">
      <span class="mark-circle"></span>
      <span class="mark-name">Corvane Capital</span>
    </div>
  </section>

  <section class="card card-front">
    <div class="front-band"></div>
    <div class="brand-block">
      <span class="brand-circle"></span>
      <span class="brand-name">Corvane Capital</span>
    </div>
    <div class="divider"></div>
    <div class="contact-block">
      <h1 class="person-name">Elliot Marsh</h1>
      <p class="person-role">Owner</p>
      <p class="address">18 Harrow Lane, Suite 4<br>30112, Aldermoor</p>
      <ul class="contact-list">
        <li>
          <svg viewBox="0 0 24 24" aria-hidden="true"><path d="M6.6 10.8a15.5 15.5 0 0 0 6.6 6.6l2.2-2.2a1 1 0 0 1 1-.25 11.4 11.4 0 0 0 3.6.57 1 1 0 0 1 1 1V20a1 1 0 0 1-1 1A17 17 0 0 1 3 4a1 1 0 0 1 1-1h3.5a1 1 0 0 1 1 1c0 1.25.2 2.45.57 3.57a1 1 0 0 1-.25 1z"/></svg>
          044-555 010 200
        </li>
        <li>
          <svg viewBox="0 0 24 24" aria-hidden="true"><path d="M2 5h20v14H2z M2 5l10 8 10-8" fill="none" stroke="#1f222c" stroke-width="2"/></svg>
          info@corvanecap.com
        </li>
        <li>
          <svg viewBox="0 0 24 24" aria-hidden="true"><circle cx="12" cy="12" r="10"/></svg>
          www.corvanecap.com
        </li>
      </ul>
    </div>
    <div class="band-mark">
      <span class="mark-circle"></span>
    </div>
  </section>
</body>
</html>
```